German Headhunter/ HR Consultancy needs Business Cards Design

We need a business Card Design for our Company in Stuttgart. We are specialized as Headhunter/ HR Consultancy in Placement of specialist and managers in permanent employment. Please refer to our business logo.

```html
<!DOCTYPE html>
<html lang="de">
<head>
<meta charset="utf-8">
<title>Kernwerk Personalberatung – Visitenkarte</title>
<link href="https://fonts.googleapis.com/css2?family=Montserrat:wght@600;700&family=Lato:wght@400;700&display=swap" rel="stylesheet">
<style>
  :root {
    --backdrop: #1f1f1f;
    --brand-blue: #3a56a8;
    --brand-blue-deep: #2a3f86;
    --paper: #ffffff;
    --arc-grey: #9a9a9a;
  }
  * { margin: 0; padding: 0; box-sizing: border-box; }
  html, body { width: 1200px; height: 1015px; overflow: hidden; }
  body {
    background: var(--backdrop);
    font-family: "Lato", sans-serif;
    position: relative;
  }
  .card {
    position: absolute;
    left: 290px;
    width: 620px;
    height: 354px;
    overflow: hidden;
    box-shadow: 0 14px 30px rgba(0,0,0,.55);
  }
  .card--back { top: 105px; background: var(--brand-blue); }
  .card--front { top: 555px; background: var(--brand-blue); }

  .wordmark {
    display: flex;
    align-items: center;
    gap: 12px;
    white-space: nowrap;
  }
  .wordmark__dot {
    flex: none;
    border-radius: 50%;
  }
  .wordmark__text {
    font-family: "Montserrat", sans-serif;
    font-weight: 700;
    letter-spacing: 2px;
    line-height: 1.05;
    text-transform: uppercase;
  }
  .wordmark__text small {
    display: block;
    font-size: .46em;
    letter-spacing: 2.2px;
  }

  .card--back .wordmark {
    position: absolute;
    left: 50%; top: 50%;
    transform: translate(-50%, -50%);
  }
  .card--back .wordmark__dot { background: var(--brand-blue-deep); width: 40px; height: 40px; }
  .card--back .wordmark__text { font-size: 40px; color: var(--brand-blue-deep); }

  .front-shapes { position: absolute; inset: 0; }

  .card--front .wordmark {
    position: absolute;
    left: 362px; top: 138px;
  }
  .card--front .wordmark__dot { background: var(--brand-blue); width: 26px; height: 26px; }
  .card--front .wordmark__text { font-size: 25px; color: var(--brand-blue); }

  .person {
    position: absolute;
    left: 40px; top: 62px;
    color: var(--paper);
  }
  .person__name {
    font-family: "Montserrat", sans-serif;
    font-weight: 700;
    font-size: 25px;
    letter-spacing: 1px;
    text-transform: uppercase;
  }
  .person__role { font-size: 17px; margin-top: 2px; }

  .contact {
    position: absolute;
    left: 40px; top: 200px;
    color: var(--paper);
    font-size: 16px;
    line-height: 1.3;
    list-style: none;
  }
  .contact__address { margin-bottom: 12px; }
  .contact__row { display: flex; align-items: center; gap: 8px; }
  .contact__row svg { width: 15px; height: 15px; flex: none; }
</style>
</head>
<body>

<section class="card card--back" aria-label="Kartenrückseite">
  <div class="wordmark">
    <span class="wordmark__dot"></span>
    <div class="wordmark__text">Kernwerk<small>Personalberatung</small></div>
  </div>
</section>

<section class="card card--front" aria-label="Kartenvorderseite">
  <svg class="front-shapes" viewBox="0 0 620 354" preserveAspectRatio="none">
    <circle cx="492" cy="150" r="215" fill="var(--arc-grey)"/>
    <circle cx="500" cy="150" r="212" fill="var(--paper)"/>
    <rect x="530" y="0" width="90" height="354" fill="var(--paper)"/>
  </svg>

  <div class="person">
    <div class="person__name">Lukas Brenner</div>
    <div class="person__role">Managing Director</div>
  </div>

  <ul class="contact">
    <li class="contact__address">18 Lindenweg,<br>Stuttgart, 70173</li>
    <li class="contact__row">
      <svg viewBox="0 0 24 24"><path fill="#fff" d="M6.6 10.8a15 15 0 0 0 6.6 6.6l2.2-2.2c.3-.3.7-.4 1-.2 1.1.4 2.3.6 3.6.6.6 0 1 .4 1 1V20c0 .6-.4 1-1 1A17 17 0 0 1 3 4c0-.6.4-1 1-1h3.5c.6 0 1 .4 1 1 0 1.3.2 2.5.6 3.6.1.3 0 .7-.2 1z"/></svg>
      0711-555 0182
    </li>
    <li class="contact__row">
      <svg viewBox="0 0 24 24"><path fill="#fff" d="M2 5h20v14H2zm2 2v.5l8 5 8-5V7zm0 2.8V17h16V9.8l-8 5z"/></svg>
      kontakt@kernwerk-hr.de
    </li>
    <li class="contact__row">
      <svg viewBox="0 0 24 24"><g fill="none" stroke="#fff" stroke-width="1.8"><circle cx="12" cy="12" r="9"/><ellipse cx="12" cy="12" rx="4" ry="9"/><path d="M3 12h18M5 7h14M5 17h14"/></g></svg>
      www.kernwerk-hr.de
    </li>
  </ul>

  <div class="wordmark">
    <span class="wordmark__dot"></span>
    <div class="wordmark__text">Kernwerk<small>Personalberatung</small></div>
  </div>
</section>

</body>
</html>
```